Lumavento business card

We need a modern business card - With our 4 colors - See web: www.lumavento.dk

I have attached logo and som old business Cards we have - Lets Make the new ones shine...:-) -

Industry/Entity Type

Business

Requirements
Must have
• the logo with lumavento only,

```html
<!DOCTYPE html>
<html lang="da">
<head>
<meta charset="utf-8">
<title>Lumavento business card</title>
<link href="https://fonts.googleapis.com/css2?family=Source+Sans+3:wght@300;400;600&display=swap" rel="stylesheet">
<style>
  :root {
    --lime: #8cc659;
    --lime-soft: #b5db92;
    --ink: #2b2b2b;
    --grey: #555a5e;
    --paper: #ffffff;
    --backdrop: #d9d9d9;
  }
  * { margin: 0; padding: 0; box-sizing: border-box; }
  html, body { width: 1105px; height: 1200px; overflow: hidden; }
  body {
    background: var(--backdrop);
    font-family: "Source Sans 3", "Helvetica Neue", Arial, sans-serif;
    position: relative;
  }
  .card {
    position: absolute;
    left: 196px;
    width: 720px;
    height: 412px;
    overflow: hidden;
    box-shadow: 0 3px 8px rgba(0,0,0,0.25);
  }
  .card--front { top: 146px; background: var(--paper); }
  .card--back { top: 602px; background: var(--lime); }

  .brand-mark {
    position: absolute;
    border-radius: 50%;
  }
  .card--front .brand-mark {
    left: 196px;
    top: 108px;
    width: 90px;
    height: 90px;
    background: var(--lime);
  }
  .card--back .brand-mark {
    left: -40px;
    top: 20px;
    width: 400px;
    height: 400px;
    background: var(--lime-soft);
  }

  .brand {
    position: absolute;
    text-align: center;
  }
  .card--front .brand { left: 105px; width: 273px; top: 220px; }
  .card--back .brand { left: 394px; width: 302px; top: 290px; }
  .brand__name {
    font-weight: 400;
    font-size: 23px;
    letter-spacing: 3px;
    line-height: 32px;
    color: var(--ink);
  }
  .brand__rule {
    height: 3px;
    background: var(--lime);
    margin-top: 14px;
  }
  .brand__tagline {
    font-size: 15px;
    margin-top: 14px;
    color: var(--ink);
  }
  .card--back .brand__name,
  .card--back .brand__tagline { color: var(--paper); }
  .card--back .brand__rule { background: var(--paper); }

  .contact {
    position: absolute;
    left: 403px;
    top: 86px;
  }
  .contact__name {
    font-size: 26px;
    font-weight: 600;
    color: var(--lime);
    line-height: 30px;
  }
  .contact__title {
    font-size: 18px;
    color: var(--ink);
    margin-top: 4px;
  }
  .contact__address {
    font-size: 18px;
    color: var(--grey);
    margin-top: 12px;
    margin-left: 3px;
    line-height: 22px;
  }
  .contact__list {
    list-style: none;
    margin-top: 13px;
    margin-left: 14px;
  }
  .contact__item {
    display: flex;
    align-items: center;
    font-size: 18px;
    color: var(--grey);
    height: 27.5px;
  }
  .contact__icon {
    width: 16px;
    height: 16px;
    margin-right: 14px;
    fill: var(--lime);
    flex: none;
  }
</style>
</head>
<body>
  <section class="card card--front">
    <div class="brand-mark" role="img" aria-label="Lumavento brand mark"></div>
    <div class="brand">
      <div class="brand__name">lumavento</div>
      <div class="brand__rule"></div>
      <div class="brand__tagline">medier til unge</div>
    </div>

    <div class="contact">
      <div class="contact__name">Jonas Bergholt</div>
      <div class="contact__title">Salgsdirektør</div>
      <div class="contact__address">Lindevej 14<br>2000 Frederiksberg</div>
      <ul class="contact__list">
        <li class="contact__item">
          <svg class="contact__icon" viewBox="0 0 16 16"><path d="M3.5 1 6 4 4.6 5.8c.9 2 2.6 3.7 4.6 4.6L11 9l3 2.5-1.5 2.8C7 14 2 9 1.7 3.5z"/></svg>
          +45 31 42 67 80
        </li>
        <li class="contact__item">
          <svg class="contact__icon" viewBox="0 0 16 16"><path d="M3.5 1 6 4 4.6 5.8c.9 2 2.6 3.7 4.6 4.6L11 9l3 2.5-1.5 2.8C7 14 2 9 1.7 3.5z"/></svg>
          +45 52 19 73 46
        </li>
        <li class="contact__item">
          <svg class="contact__icon" viewBox="0 0 16 16"><path d="M1 3.5h14v9H1z"/><path d="M1.5 4 8 9l6.5-5" fill="none" stroke="#fff" stroke-width="1.3"/></svg>
          jb@lumavento.dk
        </li>
        <li class="contact__item">
          <svg class="contact__icon" viewBox="0 0 16 16"><circle cx="8" cy="8" r="7"/><path d="M4 4.5c2 0 3 1 2.5 2.5S4 8 5 10s.5 3 0 3.5M10 2.5c0 2 1.5 2 2.5 3s0 3-1 4-1 2 0 3.5" fill="none" stroke="#fff" stroke-width="1.2"/></svg>
          www.lumavento.dk
        </li>
      </ul>
    </div>
  </section>

  <section class="card card--back">
    <div class="brand-mark" role="img" aria-label="Large Lumavento brand mark decoration"></div>
    <div class="brand">
      <div class="brand__name">lumavento</div>
      <div class="brand__rule"></div>
      <div class="brand__tagline">medier til unge</div>
    </div>
  </section>
</body>
</html>
```